Business Card - high end, modern health care

Hey designers!

We need a double sided business card for the boutique, cutting edge physical therapy rehabilitation centre in Sydney's Northern Beaches.

With the most qualified physios in the area The Harbourview Motion Clinic does what other physiotherapy practices do not, we take our time with our patients giving them longer appointments, better physios and therefor faster results!

We guarantee that the service people receive at THMC will be unparalleled.

Hence we need a business card to reflect our modern, boutique, high end service. The final design needs to reflect that we are in a class of our own yet with the feel of beachside retreat.

Below I have attached our logo in both blue on white and white on blue. The exact colour is;
and the font that we have used in our logo is Tex Gyre Aventador.

I like the idea of the blue as the main colour as it is more eye catching and our signage onto the main road will be in this blue and in the interest of consistency across marketing the blue needs to be a part of the design. However I would appreciate a few designs onto a wooden background as this is a visual theme within the fitout of the practice.

The design needs to be of standard size (91x55mm).

Target Market(s)

We target people who have an end outcome in mind and those who have had poor experiences with other providers and ensure that everyone gets the care that they deserve with a premium service that is tailored to the individuals circumstances. As a premium service, the target market is highly educated, business and tech savvy with the additional target market of elderly people who have self funded their retirement and see value in paying for the best ongoing rehabilitation to maintain independence.

Industry/Entity Type

Physical Therapy

Contact Information for Business Card

Name, designation( Titled Musculoskeletal Physiotherapist... there will also be those in the company that have multiple designations ie 5 or 6 words long), phone number, email, facebook, instagram, address

Font styles to use
Sans Serif

Colors

Designer to choose colors to be used in the design.

Requirements
Must have
• Front - The logo as large as possible, blue or wooden theme, and all of the important details.
• Back - A blank space/lines on which to write appointment times (no "Appointment, date, time" etc.)
Nice to have
• facebook url
• logos for facebook and instagram
• Mini logos for the phone and email?

```html
<!DOCTYPE html>
<html lang="en">
<head>
<meta charset="utf-8">
<title>The Harbourview Motion Clinic – Business Card</title>
<link href="https://fonts.googleapis.com/css2?family=Roboto:wght@500;700&family=Roboto+Condensed:wght@400;500&display=swap" rel="stylesheet">
<style>
  :root {
    --page-bg: #2a2a2a;
    --card-white: #eeeeee;
    --brand-blue: #0b56ac;
    --edge-dark: #1b1b1b;
    --text-light: #f4f6fa;
  }
  * { box-sizing: border-box; margin: 0; padding: 0; }
  html, body { width: 1200px; height: 900px; overflow: hidden; }
  body {
    background: var(--page-bg);
    display: flex;
    flex-direction: column;
    align-items: center;
    justify-content: center;
    gap: 40px;
    font-family: "Roboto", Arial, sans-serif;
  }
  .card {
    position: relative;
    width: 660px;
    height: 399px;
    overflow: hidden;
    box-shadow: 0 10px 30px rgba(0,0,0,.45);
  }

  /* Back side */
  .card-back { background: var(--card-white); }
  .brand {
    position: absolute;
    left: 0; right: 0;
    display: flex;
    flex-direction: column;
    align-items: center;
    color: var(--brand-blue);
    font-weight: 700;
    text-transform: uppercase;
    text-align: center;
  }
  .brand-dot { border-radius: 50%; background: var(--brand-blue); }
  .card-back .brand { top: 26px; }
  .card-back .brand-dot { width: 104px; height: 104px; margin-bottom: 16px; }
  .card-back .brand-name { font-size: 19px; line-height: 1.1; letter-spacing: .5px; }
  .rule-pair {
    position: absolute;
    left: 0; right: 0; top: 224px;
    height: 9px;
    border-top: 2px solid var(--brand-blue);
    border-bottom: 2px solid var(--brand-blue);
  }
  .appointment {
    position: absolute;
    left: 110px; top: 286px;
    display: flex;
    align-items: center;
    gap: 12px;
    color: var(--brand-blue);
    font-size: 17px;
    font-weight: 500;
  }
  .appointment-line {
    width: 220px;
    border-bottom: 1.5px dashed var(--brand-blue);
    margin-left: 4px;
    transform: translateY(5px);
  }

  /* Front side */
  .card-front { background: var(--brand-blue); }
  .front-shape { position: absolute; inset: 0; }
  .card-front .brand { left: 40px; right: auto; width: 230px; top: 78px; }
  .card-front .brand-dot { width: 150px; height: 150px; margin-bottom: 16px; }
  .card-front .brand-name { font-size: 21px; line-height: 1.1; }
  .person {
    position: absolute;
    right: 58px; top: 28px;
    text-align right;
    text-align: right;
    color: var(--text-light);
  }
  .person-name { font-size: 28px; font-weight: 700; letter-spacing: .3px; }
  .person-role { font-family: "Roboto Condensed", Arial, sans-serif; font-size: 19px; margin-top: 2px; }
  .treatment-art {
    position: absolute;
    right: 50px; top: 108px;
    width: 196px; height: 62px;
    background: linear-gradient(90deg, rgba(255,255,255,.55), rgba(255,255,255,.4));
    border-radius: 4px;
  }
  .contacts {
    position: absolute;
    right: 50px; top: 195px;
    list-style: none;
    font-family: "Roboto Condensed", Arial, sans-serif;
    font-size: 18px;
    color: var(--text-light);
  }
  .contact {
    display: flex;
    justify-content: flex-end;
    align-items: center;
    gap: 10px;
    height: 37px;
  }
  .contact-icon {
    width: 20px; height: 20px;
    background: var(--text-light);
    border-radius: 3px;
    display: flex; align-items: center; justify-content: center;
    flex: none;
  }
  .contact-icon svg { width: 14px; height: 14px; }
</style>
</head>
<body>

  <section class="card card-back" aria-label="Card back">
    <div class="brand">
      <span class="brand-dot"></span>
      <span class="brand-name">The Harbourview<br>Motion Clinic</span>
    </div>
    <div class="rule-pair"></div>
    <div class="appointment">
      <svg width="48" height="26" viewBox="0 0 48 26" aria-hidden="true">
        <path d="M0 0 L48 13 L0 26 L9 13 Z" fill="var(--brand-blue)"/>
      </svg>
      <span class="appointment-label">Appointment Times:</span>
      <span class="appointment-line"></span>
    </div>
  </section>

  <section class="card card-front" aria-label="Card front">
    <svg class="front-shape" viewBox="0 0 660 399" preserveAspectRatio="none" aria-hidden="true">
      <path d="M0 0 H285 Q355 190 300 399 H0 Z" fill="var(--edge-dark)"/>
      <path d="M0 0 H268 Q340 190 285 399 H0 Z" fill="var(--card-white)"/>
    </svg>

    <div class="brand">
      <span class="brand-dot"></span>
      <span class="brand-name">The Harbourview<br>Motion Clinic</span>
    </div>

    <div class="person">
      <p class="person-name">DANIEL REEVE</p>
      <p class="person-role">physiotherapist</p>
    </div>

    <div class="treatment-art" role="img" aria-label="Two white pictograms of a physiotherapist treating a patient on a table"></div>

    <ul class="contacts">
      <li class="contact">+00 120 450 780
        <span class="contact-icon"><svg viewBox="0 0 14 14" aria-hidden="true"><path d="M3 1 L5.5 1 L6.5 4 L5 5.2 Q6.3 8 8.8 9 L10 7.5 L13 8.5 L13 11 Q12.5 13 10.5 13 Q2 12 1 3.5 Q1 1.5 3 1 Z" fill="var(--brand-blue)"/></svg></span>
      </li>
      <li class="contact">hello@motionclinic.com
        <span class="contact-icon"><svg viewBox="0 0 14 14" aria-hidden="true"><rect x="1" y="3" width="12" height="8" fill="none" stroke="var(--brand-blue)" stroke-width="1.5"/><path d="M1 3 L7 8 L13 3" fill="none" stroke="var(--brand-blue)" stroke-width="1.5"/></svg></span>
      </li>
      <li class="contact">Social/MotionClinic <span class="contact-icon"></span></li>
      <li class="contact">@motionclinic <span class="contact-icon"></span></li>
    </ul>
  </section>

</body>
</html>
```